Kestrel Facilities Business Card Design

We would now like to design business cards with the new Kestrel Facilities logo

Target Market(s)

Professional

Industry/Entity Type

Professional services

Contact Information for Business Card

Employee name, title, phone number, email address, corporate office address and logo.

Font styles to use
Sans Serif

Colors
0054AA
0677BA
7BADD7
CADEEF
E8F1F8

Requirements
Must have
• My logo
Should not have
• any other pictures or images besides my logo

```html
<!DOCTYPE html>
<html lang="en">
<head>
<meta charset="utf-8">
<title>Kestrel Facilities Business Card</title>
<link href="https://fonts.googleapis.com/css2?family=Montserrat:wght@400;600;700&display=swap" rel="stylesheet">
<style>
  :root {
    --brand-blue: #0677BA;
    --brand-deep: #0054AA;
    --ink: #2b2b2b;
    --card-white: #ffffff;
    --card-black: #1c1c1e;
    --pattern-tone: #2a2a2d;
    --backdrop: #d9d9dc;
  }
  * { margin: 0; padding: 0; box-sizing: border-box; }
  html, body { width: 1200px; height: 930px; overflow: hidden; }
  body {
    background: var(--backdrop);
    font-family: "Montserrat", sans-serif;
    display: flex;
    flex-direction: column;
    align-items: center;
    justify-content: center;
    gap: 40px;
  }
  .card {
    width: 700px;
    height: 400px;
    border-radius: 22px;
    position: relative;
    overflow: hidden;
    box-shadow: 0 6px 18px rgba(0,0,0,0.18);
  }
  /* Back side */
  .card-back { background: var(--card-black); }
  .card-back .pattern-field {
    position: absolute; inset: 0;
    background: linear-gradient(135deg, var(--pattern-tone), var(--card-black));
  }
  .card-back .back-mark {
    position: absolute; inset: 0;
    display: flex; align-items: center; justify-content: center;
    color: var(--brand-blue);
    font-weight: 700;
    font-size: 26px;
    letter-spacing: 1px;
  }
  /* Front side */
  .card-front {
    background: var(--card-white);
    display: flex;
    align-items: center;
    padding: 0 50px 0 60px;
  }
  .brand-block {
    width: 260px;
    display: flex;
    align-items: center;
    gap: 14px;
  }
  .brand-square {
    width: 34px; height: 34px;
    background: var(--brand-blue);
    flex: none;
  }
  .brand-name {
    color: var(--brand-blue);
    font-weight: 700;
    font-size: 30px;
    line-height: 1.1;
  }
  .divider {
    width: 2px;
    height: 190px;
    background: var(--brand-blue);
    margin: 0 34px 0 24px;
    flex: none;
  }
  .contact-block { color: var(--ink); font-size: 17px; line-height: 1.45; }
  .person-name {
    color: var(--brand-blue);
    font-weight: 700;
    font-size: 26px;
    letter-spacing: 0.5px;
    line-height: 1.1;
  }
  .person-title { margin-bottom: 16px; }
  .address { margin-bottom: 16px; }
  .contact-line { display: flex; align-items: center; gap: 10px; }
  .contact-line svg { width: 14px; height: 14px; flex: none; }
</style>
</head>
<body>
  <section class="card card-back">
    <div class="pattern-field" role="img" aria-label="Dark repeating brand monogram pattern"></div>
    <div class="back-mark">Kestrel Facilities</div>
  </section>

  <section class="card card-front">
    <div class="brand-block">
      <span class="brand-square"></span>
      <span class="brand-name">Kestrel Facilities</span>
    </div>
    <div class="divider"></div>
    <div class="contact-block">
      <div class="person-name">DANIEL WHITFORD</div>
      <div class="person-title">Director</div>
      <div class="address">218 Cedar Ridge Lane<br>Salem, OR 97301</div>
      <div class="contact-line">
        <svg viewBox="0 0 24 24" aria-hidden="true"><path fill="#0677BA" d="M6.6 10.8a15.1 15.1 0 0 0 6.6 6.6l2.2-2.2c.3-.3.7-.4 1-.2 1.1.4 2.3.6 3.6.6.6 0 1 .4 1 1V20c0 .6-.4 1-1 1A17 17 0 0 1 3 4c0-.6.4-1 1-1h3.5c.6 0 1 .4 1 1 0 1.3.2 2.5.6 3.6.1.3 0 .7-.2 1z"/></svg>
        (555) 218-4630
      </div>
      <div class="contact-line">
        <svg viewBox="0 0 24 24" aria-hidden="true"><rect x="3" y="5" width="18" height="14" fill="none" stroke="#0677BA" stroke-width="2"/><path d="M3 6l9 7 9-7" fill="none" stroke="#0677BA" stroke-width="2"/></svg>
        info@kestrelfacilities.com
      </div>
    </div>
  </section>
</body>
</html>
```